FieldNest.com FACELIFT design for the online store

A) GENERAL
We need a small FACELIFT design with a short styleguide for our online store http://FieldNest.com (online store for sport goods; the store is just now in responsive design; actually only in German). The store is the first online store worldwide with 3d images for all products.
B) Designers: PLEASE NOTE:
- We don't want change functionality!
- We only want a small facelift.
- We don't need a fully coded website.
C) We only need for the responsive design views:
1. the home page design (one page)
http://www.fieldnest.com/de/
2. the category listing design (one page)
http://www.fieldnest.com/de/alle/running.html
3. the product detail page (one page)
http://www.fieldnest.com/de/varnok-tz-max-3d-qrt-herren-traillaufschuhe-dura-flex.html
4. the cms page (textonly !!!)
http://www.fieldnest.com/de/versand-und-lieferung
5. the Mega drop down
D) We intend to change/use:
- maybe to use a background image in the start page, and each category
- change the header
- change the font sizes for the titles (maybe in capital letters)
- change the mega drop down

```html
<!DOCTYPE html>
<html lang="en">
<head>
<meta charset="utf-8">
<title>FieldNest.com – Home</title>
<link rel="stylesheet" href="https://fonts.googleapis.com/css2?family=Open+Sans:wght@300;400;600;700&display=swap">
<style>
:root{
  --ink:#222;
  --dark:#2b2b2b;
  --darker:#1c1c1c;
  --footer:#262626;
  --line:#dcdcdc;
  --muted:#9a9a9a;
  --white:#fff;
  --hero-a:#d8d8d8;
  --hero-b:#a9a9a9;
}
*{box-sizing:border-box;margin:0;padding:0}
html,body{width:901px;height:1200px;overflow:hidden;background:var(--white);font-family:"Open Sans",sans-serif;color:var(--ink)}
.page{position:relative;width:901px;height:1200px}
.hero{position:absolute;left:0;top:0;width:901px;height:458px;background:linear-gradient(90deg,var(--hero-a),#c4c4c4 50%,var(--hero-b))}
.hero-photo{position:absolute;left:480px;top:50px;width:300px;height:408px;background:linear-gradient(180deg,#9a9a9a 0%,#b5625b 60%,#c0323a 100%);opacity:.5;border-radius:140px 140px 0 0}
.header{position:absolute;left:74px;top:0;width:707px;height:50px;background:var(--white);display:flex;align-items:center}
.brand{margin-left:12px;font-size:20px;font-weight:700;letter-spacing:1px;color:#111}
.header-links{margin-left:auto;display:flex;align-items:center;font-size:9px;color:#555}
.header-links span{padding:0 10px;border-right:1px solid var(--line)}
.header-links span:last-child{border:0}
.search{width:143px;height:23px;border:1px solid var(--line);margin:0 12px 0 2px;font-size:8px;color:var(--muted);display:flex;align-items:center;justify-content:space-between;padding:0 8px}
.cart{position:absolute;left:781px;top:0;width:45px;height:50px;background:var(--dark);color:var(--white);font-size:10px;text-align:center;padding-top:8px}
.side-menu{position:absolute;left:74px;top:167px;width:180px}
.side-menu div{height:38px;margin-bottom:3px;background:var(--dark);color:var(--white);font-size:18px;font-weight:300;display:flex;align-items:center;padding-left:12px}
.side-menu div.active{background:#eee;color:#333}
.side-menu i{width:13px;height:13px;border:1px solid currentColor;border-radius:50%;margin-right:10px;opacity:.6}
.hero-title{position:absolute;left:325px;top:172px;color:var(--white);line-height:.98;text-shadow:0 1px 2px rgba(0,0,0,.15)}
.hero-title b{display:block;font-size:52px;font-weight:700}
.hero-title span{display:block;font-size:48px;font-weight:300}
.arrow{position:absolute;top:234px;width:20px;height:25px;background:#8a8a8a;color:#ddd;font-size:14px;text-align:center;line-height:25px}
.nav{position:absolute;left:0;top:458px;width:901px;height:35px;background:var(--darker);display:flex;padding-left:90px;align-items:center;font-size:9.5px;color:#bbb}
.nav span{margin-right:28px}
.nav span.on{color:var(--white)}
.section-title{position:absolute;left:74px;top:526px;font-size:15px;font-weight:600}
.next{position:absolute;left:818px;top:523px;color:#aaa;font-size:14px}
.products{position:absolute;left:74px;top:561px;display:flex;gap:4px}
.card{width:147px;height:201px;border:1px solid var(--line)}
.card .img{height:140px;background:radial-gradient(circle,#bfc9c9,#fff 70%)}
.card .info{height:60px;background:var(--dark);color:var(--white);text-align:center;font-size:8px;padding-top:14px;line-height:1.3}
.card .info b{display:block;font-size:10px;font-weight:400;margin-top:5px}
.brands{position:absolute;left:74px;top:789px;width:752px;height:59px;border-top:1px solid var(--line);border-bottom:1px solid var(--line);display:flex;align-items:center;justify-content:space-around;padding:0 20px;font-size:12px;font-weight:600;color:#444}
.perks{position:absolute;left:74px;top:852px;display:flex;gap:2px}
.perks div{width:249px;height:30px;background:#e4e4e4;font-size:12.5px;color:#333;display:flex;align-items:center;justify-content:center;gap:8px}
.footer{position:absolute;left:0;top:920px;width:901px;height:212px;background:var(--footer);color:#ccc}
.fcol{position:absolute;top:22px}
.fcol h3{font-size:13px;font-weight:400;color:var(--white);margin-bottom:10px}
.fcol p{font-size:8px;line-height:1.6;color:#aaa}
.badges{display:flex;gap:8px}
.badges i{width:33px;height:33px;border-radius:50%;background:#8f8f8f;display:block}
.social{display:flex;gap:7px}
.social i{width:20px;height:20px;border-radius:50%;background:#666;display:block}
.links{display:grid;grid-template-columns:105px 105px;font-size:7.5px;color:#aaa;row-gap:8px}
.links span:before{content:"• "}
.vline{position:absolute;top:26px;width:1px;height:152px;background:#444}
.nl-input{width:117px;height:20px;background:var(--white);font-size:7.5px;color:#888;display:flex;align-items:center;justify-content:space-between;padding-left:6px}
.nl-input b{width:26px;height:20px;background:#ccc}
.promo{margin-top:16px;width:115px;height:40px;background:#d5d5d5;display:flex;align-items:center;gap:4px;padding-left:3px;font-size:8px;font-weight:700;color:#222;line-height:1.2}
.promo i{width:30px;height:30px;border-radius:50%;background:#1f5f8a;color:#fff;font-style:normal;font-size:10px;display:flex;align-items:center;justify-content:center}
.cards{display:flex;gap:4px;margin-top:18px}
.cards i{width:19px;height:12px;background:#777;display:block}
.bottom{position:absolute;left:0;top:1132px;width:901px;height:68px;background:#1a1a1a;font-size:7.5px;color:#999}
.bottom .copy{position:absolute;left:74px;top:24px}
.bottom .legal{position:absolute;left:74px;top:44px}
.bottom .ctrl{position:absolute;left:778px;top:24px;display:flex;gap:6px}
.bottom .ctrl i{width:21px;height:21px;border:1.5px solid #ccc;border-radius:50%;display:block}
</style>
</head>
<body>
<div class="page">
  <div class="hero" role="img" aria-label="Cyclist in helmet and red jersey against grey studio backdrop"><div class="hero-photo"></div></div>
  <header class="header">
    <div class="brand">FieldNest.com</div>
    <div class="header-links"><span>&#128274; Sign in</span><span>&#9776; Wishlist</span><span>English &#9662;</span></div>
    <div class="search">Search <svg width="9" height="9" viewBox="0 0 10 10"><circle cx="4" cy="4" r="3" fill="none" stroke="#999" stroke-width="1.3"/><line x1="6.2" y1="6.2" x2="9" y2="9" stroke="#999" stroke-width="1.3"/></svg></div>
  </header>
  <div class="cart">0<br><svg width="12" height="11" viewBox="0 0 12 11"><path d="M0 1h2l2 6h6l2-5H3" fill="#fff"/><circle cx="4.5" cy="9.5" r="1.2" fill="#fff"/><circle cx="9" cy="9.5" r="1.2" fill="#fff"/></svg></div>
  <div class="arrow" style="left:0">&#8249;</div>
  <div class="arrow" style="left:881px">&#8250;</div>
  <nav class="side-menu">
    <div class="active"><i></i>Men’s</div>
    <div><i></i>Women’s</div>
    <div><i></i>Children / Youth</div>
    <div><i></i>Gift Ideas</div>
  </nav>
  <div class="hero-title"><b>BIKE</b><span>Oster</span><span>Aktion</span></div>
  <nav class="nav"><span class="on">Outdoor</span><span>Rock Climbing</span><span>Running</span><span>Bike</span><span>Ski &amp; Freeride</span><span>Ski touring</span><span>Fitness</span><span>Fashion</span><span>Digital</span><span>Remaining Stock</span><span>%Deals</span></nav>
  <h2 class="section-title">Top products</h2>
  <div class="next">&#8250;</div>
  <div class="products">
    <div class="card"><div class="img" role="img" aria-label="Light blue running shoes"></div><div class="info">Veloran Glide 7 Damen<br>Laufschuhe<b>94,99 €</b></div></div>
    <div class="card"><div class="img" role="img" aria-label="Climbing belay device" style="background:radial-gradient(circle,#aaa,#fff 70%)"></div><div class="info">Veloran Glide 7 Damen<br>Laufschuhe<b>94,99 €</b></div></div>
    <div class="card"><div class="img" role="img" aria-label="Black mountain bike" style="background:radial-gradient(circle,#888,#fff 70%)"></div><div class="info">Veloran Glide 7 Damen<br>Laufschuhe<b>94,99 €</b></div></div>
    <div class="card"><div class="img" role="img" aria-label="White full-face bike helmet" style="background:radial-gradient(circle,#ddd,#fff 70%)"></div><div class="info">Veloran Glide 7 Damen<br>Laufschuhe<b>94,99 €</b></div></div>
    <div class="card"><div class="img" role="img" aria-label="Red and yellow mountaineering boots" style="background:radial-gradient(circle,#d9863a,#fff 70%)"></div><div class="info">Veloran Glide 7 Damen<br>Laufschuhe<b>94,99 €</b></div></div>
  </div>
  <div class="brands"><span style="color:#ccc">&#8249;</span><span>Halvard</span><span>Quillon</span><span>Morrow</span><span>Tremont</span><span>Sollara</span><span>Vexel</span><span>Nordak</span><span>Weatherlin</span><span style="color:#ccc">&#8250;</span></div>
  <div class="perks">
    <div><svg width="14" height="10" viewBox="0 0 14 10"><rect x="0" y="1" width="8" height="6" fill="#333"/><path d="M8 3h3l2 2v2H8z" fill="#333"/><circle cx="3" cy="8.5" r="1.4" fill="#333"/><circle cx="11" cy="8.5" r="1.4" fill="#333"/></svg>FREE SHIPPING FROM 40 €</div>
    <div><svg width="12" height="12" viewBox="0 0 12 12"><path d="M0 0h6l6 6-6 6-6-6z" fill="#333"/><circle cx="3" cy="3" r="1" fill="#e4e4e4"/></svg>FINAL WINTER SALE UP TO 70%</div>
    <div><svg width="12" height="12" viewBox="0 0 12 12"><path d="M10 6a4 4 0 1 1-1.2-2.8" fill="none" stroke="#333" stroke-width="1.8"/><path d="M7 1h4v4z" fill="#333"/></svg>FREE RETURNS</div>
  </div>
  <footer class="footer">
    <div class="fcol" style="left:74px">
      <h3>Contact us</h3>
      <div class="badges"><i></i><i></i><i style="border-radius:6px"></i></div>
      <h3 style="margin-top:14px">Follow us on</h3>
      <div class="social"><i></i><i></i><i></i><i></i></div>
    </div>
    <div class="vline" style="left:206px"></div>
    <div class="fcol" style="left:227px;width:200px">
      <h3>About us</h3>
      <p>As a specialist in clothing and sports equipment in the outdoor, mountaineering, climbing and skiing as well as cycling and gym we inspire our customers throughout Europe with cheap price and product 3D worlds. This offer our top brands Brisken, Tollwyn, Greyhorn, Lindqvale, Nordak, Pemberly, Halvard, Caldera Coast, Varnok, Quillon, Bramfield, Vexel and Ardent Sports a range of the highest quality.</p>
    </div>
    <div class="vline" style="left:446px"></div>
    <div class="fcol" style="left:475px">
      <h3>Quick Links</h3>
      <div class="links">
        <span>Shipping and Delivery</span><span>About FieldNest.com</span>
        <span>Payment Methods</span><span>Our stores Overview</span>
        <span>Return</span><span>Jobs</span>
        <span>Service | Help | FAQs</span><span>Terms and Conditions</span>
        <span>Privacy Policy</span><span>Site Map</span>
        <span>Recommendations</span><span>Searches</span>
        <span>Experiences</span><span>Imprint</span>
        <span>Contact</span>
      </div>
    </div>
    <div class="vline" style="left:688px"></div>
    <div class="fcol" style="left:709px">
      <h3>Newsletter</h3>
      <div class="nl-input">E-mail<b></b></div>
      <div class="promo"><i>5€</i><span>JETZT ANMELDEN!<br>und 5 € sichern!</span></div>
      <div class="cards"><i></i><i></i><i></i><i></i></div>
    </div>
  </footer>
  <div class="bottom">
    <div class="copy">Copyright © 2015 FieldNest. All Rights Reserved.</div>
    <div class="legal">Disclaimer &nbsp;|&nbsp; Support &nbsp;|&nbsp; Sitemap</div>
    <div class="ctrl"><i></i><i></i></div>
  </div>
</div>
</body>
</html>
```